Modern, clean and professional Wordpress design for a safety training company!

We are currently in the process of creating a new website for our business. We have hired a website developer and the main structure of our new Wordpress site is complete. We now need an overall design plan for the site. We need a very clean, professional and easy to follow website. Most of our website visitors only spend about 30-45 secs on our sites "shopping " so it is imperative that we have a strong Home Page.
Our company specializes in CPR and First Aid Certification Classes to businesses and individuals throughout Northern California. We provide these certifications two ways: ONSITE-We come to you, and HOSTED-we offer weekly classes at our 2 locations.
Our design needs to use the general green and blue colors of our logo. But we also like white.
The final design MUST communicate a legitimate, trustworthy and professional business. Our industry is VERY competitive and we need to STAND OUT.
Currently, the NEW website that we need a new design for is www.LifelineDrillWorks.com
Our old website is www.RescuePrepValleyHub.com and we really do like the design of this website, but we just needed a Wordpress site for SEO purposes.
These are 3 websites that we really:
http://morvaliontech.com/
http://www.tralbex.com/
https://www.plivant.com/
I have attached our Logo and other images if you need to use them but looking at the current two sites will be you best help.
Target Market(s)
1) Large businesses and industries that are looking for a company to provide ONSITE safety training classes at their office or place of work.
2) Individuals that need certifications for their jobs and other needs. These individuals are looking for a legitimate, trustworthy and professional environment to complete their training class.

```html
<!DOCTYPE html>
<html lang="en">
<head>
<meta charset="utf-8">
<title>Northline Safety Academy</title>
<link href="https://fonts.googleapis.com/css2?family=Raleway:wght@400;500;600&family=Open+Sans:wght@400;600&display=swap" rel="stylesheet">
<style>
:root{
  --green:#8fc31f;
  --green-dark:#6fa10e;
  --green-text:#8cb820;
  --blue:#1d3f8f;
  --blue-deep:#163473;
  --navy:#1b2f6b;
  --ink:#333;
  --muted:#555;
  --line:#d8d8d8;
  --footer:#efefef;
  --footer-bar:#e4e4e4;
  --star:#f07a1a;
}
*{margin:0;padding:0;box-sizing:border-box}
html,body{width:802px;height:1200px;overflow:hidden;background:#fff}
body{position:relative;font-family:"Open Sans",sans-serif;color:var(--ink)}
.abs{position:absolute}
/* header */
.brand{left:113px;top:22px;font-family:"Raleway",sans-serif;font-weight:600;color:var(--blue);line-height:1.05;display:flex;align-items:center;gap:8px}
.brand-mark{width:16px;height:16px;background:var(--green);border-radius:50%}
.brand-name{font-size:19px}
.brand-name small{display:block;font-size:19px}
.contact{right:114px;top:47px;text-align:left}
.contact .row{display:flex;align-items:center;gap:6px;color:var(--navy)}
.contact .phone{font-family:"Raleway",sans-serif;font-size:15px;font-weight:500}
.contact .mail{font-size:8.5px;margin-top:2px}
/* nav */
.nav{left:0;top:91px;width:802px;height:31px;background:linear-gradient(#9fd12a,#7fb314);display:flex;padding-left:113px}
.nav a{color:#fff;text-decoration:none;font-family:"Raleway",sans-serif;font-size:8.5px;font-weight:500;line-height:31px;padding:0 12px;border-right:1px solid rgba(255,255,255,.25)}
.nav a:last-child{border-right:none}
/* hero */
.hero{left:0;top:122px;width:802px;height:314px;background:linear-gradient(120deg,#6a6e72 0%,#8a8680 35%,#a09a92 55%,#4a5a80 80%,#1e2f6a 100%)}
.hero-box{left:114px;top:202px;width:234px;height:106px;background:rgba(29,63,143,.85);border-radius:2px;padding:16px 21px;color:#fff}
.hero-box h1{font-family:"Raleway",sans-serif;font-weight:500;font-size:21px;line-height:1.15}
.hero-box h2{font-family:"Raleway",sans-serif;font-weight:500;font-size:16px;margin-top:2px}
.hero-box p{font-size:5.8px;line-height:1.9;margin-top:5px;opacity:.9}
.dots{left:378px;top:373px;display:flex;gap:5px}
.dots span{width:10px;height:10px;border-radius:50%;background:#fff}
/* offers */
.offers{left:114px;top:395px;width:574px;height:137px;background:#f3f3f3;border-radius:3px;box-shadow:0 1px 3px rgba(0,0,0,.08)}
.card{top:407px;width:180px;height:125px;color:#fff;text-align:center;padding-top:14px}
.card.blue{background:linear-gradient(160deg,#3656a8,#1f3d8d)}
.card.green{background:linear-gradient(160deg,#a5d431,#86ba18)}
.card h3{font-family:"Raleway",sans-serif;font-weight:400;font-size:15px}
.card p{font-size:7.5px;line-height:16px;opacity:.9}
.card .btn{display:inline-block;margin-top:5px;border:2px solid #fff;font-size:7.5px;padding:4px 9px;border-radius:2px;color:#fff;background:rgba(0,0,0,.08)}
.card.blue .btn{background:var(--blue-deep)}
.card.green .btn{background:var(--green-dark)}
/* welcome */
.welcome{left:121px;top:576px;width:560px;text-align:center}
.welcome h2{font-family:"Raleway",sans-serif;font-weight:400;font-size:22px;color:#222}
.welcome .lead{font-family:"Raleway",sans-serif;font-size:11px;color:#444;margin-top:7px}
.welcome .body{font-size:6px;line-height:1.9;color:var(--muted);margin-top:8px}
.welcome .body + .body{margin-top:3px}
.divider{left:121px;top:710px;width:566px;height:1px;background:var(--line)}
/* featured */
.col-title{font-family:"Raleway",sans-serif;font-weight:500;font-size:14px}
.featured-title{left:117px;top:737px;color:var(--blue)}
.reviews-title{left:430px;top:737px;color:#222}
.item{left:117px;width:280px;display:flex;gap:9px}
.thumb{width:111px;height:76px;flex:none}
.item h4{font-size:7.6px;font-weight:400;line-height:1.6;color:#333}
.item p{font-size:5.9px;line-height:2.05;color:var(--muted);margin-top:3px}
.review{left:430px;width:258px}
.review h4{font-family:"Raleway",sans-serif;font-weight:400;font-size:9.3px;color:var(--green-text)}
.review p{font-size:5.9px;line-height:2.05;color:var(--muted);margin-top:3px}
.stars{display:flex;gap:2px;margin-top:3px}
/* footer */
.footer{left:0;top:990px;width:802px;height:162px;background:var(--footer)}
.foot-col{top:1020px}
.foot-col h5{font-family:"Raleway",sans-serif;font-weight:600;font-size:8.8px;color:#333;margin-bottom:7px}
.foot-col li{list-style:none;font-size:7.2px;line-height:14.8px;color:#444}
.map{left:450px;top:1037px;width:158px;height:82px;background:linear-gradient(135deg,#dcdad4,#cfcdc6);border-radius:2px}
.map-card{left:454px;top:1040px;width:126px;height:20px;background:#fff;padding:2px 5px;font-size:5.5px;color:#222;box-shadow:0 1px 2px rgba(0,0,0,.15)}
.map-card span{display:block;color:#3a6fd8;font-size:4.8px;margin-top:1px}
.badge{left:642px;top:1048px;width:40px;height:65px;background:#fff;border:1px solid #9aa8c8;border-radius:3px}
.badge i{position:absolute;left:3px;right:3px;bottom:3px;height:10px;background:var(--navy)}
.bottom{left:0;top:1152px;width:802px;height:48px;background:var(--footer-bar)}
.copy{left:126px;top:1169px;font-size:6.6px;color:#555}
.social{left:640px;top:1165px;display:flex;gap:4px}
.social span{width:12px;height:12px;border-radius:2px}
</style>
</head>
<body>

<header>
  <div class="abs brand"><span class="brand-mark"></span><div class="brand-name">Northline Safety<small>Academy</small></div></div>
  <div class="abs contact">
    <div class="row phone">
      <svg width="11" height="11" viewBox="0 0 24 24"><path fill="#7fb314" d="M6.6 10.8a15.1 15.1 0 0 0 6.6 6.6l2.2-2.2c.3-.3.7-.4 1-.2 1.1.4 2.3.6 3.6.6.6 0 1 .4 1 1V20c0 .6-.4 1-1 1C10.6 21 3 13.4 3 4c0-.6.4-1 1-1h3.5c.6 0 1 .4 1 1 0 1.3.2 2.5.6 3.6.1.3 0 .7-.2 1z"/></svg>
      916-555-0182
    </div>
    <div class="row mail">
      <svg width="10" height="8" viewBox="0 0 20 14"><rect width="20" height="14" rx="1" fill="#7fb314"/><path d="M1 1l9 7 9-7" stroke="#fff" stroke-width="1.6" fill="none"/></svg>
      info@northlinesafety.com
    </div>
  </div>
  <nav class="abs nav">
    <a>HOME</a><a>ABOUT US</a><a>CLASS CALENDER</a><a>CLASSES OF GROUPS</a><a>CERTIFICATION CLASSES</a><a>POLICIES</a><a>CONTACT</a>
  </nav>
</header>

<section>
  <div class="abs hero" role="img" aria-label="Photo of trainees practising CPR with a defibrillator on a casualty"></div>
  <div class="abs hero-box">
    <h1>CPR and First Aid</h1>
    <h2>Certification Classes</h2>
    <p>Vivamus porttitor purus nisi eleifend libero a tempus libero lectus feugiat felis Morbi diam mauris viverra in gravida eu</p>
  </div>
  <div class="abs dots"><span></span><span></span><span></span><span></span></div>

  <div class="abs offers"></div>
  <div class="abs card blue" style="left:121px" role="img" aria-label="CPR class photo tinted blue">
    <h3>CPR</h3><p>$39</p><p>Adult/Child/Infant</p><p>90 Minutes!</p><span class="btn">Register Now</span>
  </div>
  <div class="abs card green" style="left:311px" role="img" aria-label="BLS class photo tinted green">
    <h3>BLS</h3><p>$49</p><p>Healthcare/Dental</p><p>90 Minutes!</p><span class="btn">Register Now</span>
  </div>
  <div class="abs card blue" style="left:500px" role="img" aria-label="CPR and first aid class photo tinted blue">
    <h3>CPR+First Aid</h3><p>$59</p><p>Adult/Child/Infant</p><p>90 Minutes!</p><span class="btn">Register Now</span>
  </div>
</section>

<section class="abs welcome">
  <h2>Welcome to Northline Safety Academy!</h2>
  <p class="lead">Lorem ipsum dolor sit amet consectetuer adipiscing elit Nam cursus</p>
  <p class="body">Northline Safety Academy is Northern California's leader in CPR, BLS, and Basic First Aid Certifications! Taught by experienced Firefighters, our classes are much shorter and provide common sense knowledge and skills to each student to help prepare them for actual emergencies.</p>
  <p class="body">By using real life emergency responders, we have revolutionized the standard, boring CPR class by teaching students the need-to-know information and preparing them with facts and tips to help them in true life and death situations!</p>
</section>
<div class="abs divider"></div>

<h3 class="abs col-title featured-title">Featured Trainings</h3>
<div class="abs item" style="top:768px">
  <div class="thumb" role="img" aria-label="Photo of an instructor demonstrating chest compressions outdoors" style="background:linear-gradient(135deg,#5c7a45,#9aa7a8)"></div>
  <div><h4>Vivamus porttitor purus nisi eleifend libero tempus libero lectus feugiat felis</h4>
  <p>mattis in ante Morbi eget arcu Morbi porta libero id ullamcorper nonummy nibh ligula pulvinar metus eget consectetuer augue nisi quis lacus Ut ac mi quis lacus mollis aliquam Curabitur iaculis</p></div>
</div>
<div class="abs item" style="top:862px">
  <div class="thumb" role="img" aria-label="Photo of a training defibrillator unit in a classroom" style="background:linear-gradient(135deg,#3e4f6a,#a8b0bc)"></div>
  <div><h4>Sed metus augue convallis et vehicula ut pulvinar eu ante Integer</h4>
  <p>mattis in ante Morbi eget arcu Morbi porta libero id ullamcorper nonummy nibh ligula pulvinar metus eget consectetuer augue nisi quis lacus Ut ac mi quis lacus mollis aliquam Curabitur iaculis</p></div>
</div>

<h3 class="abs col-title reviews-title">Reviews &amp; Blog</h3>
<div class="abs review" style="top:765px">
  <h4>Class aptent taciti sociosqu ad litora</h4>
  <p>Morbi ornare gravida elit Integer congue augue et malesuada iaculis ipsum dui aliquet felis at cursus magna nisl nec elit Praesent elementum elit at tellus nec ultricies sit amet porttitor mattis enim In massa libero interdum nec interdum nulla</p>
  <div class="stars"><svg width="46" height="8" viewBox="0 0 46 8"><g fill="var(--star)"><path id="s" d="M4 0l1.2 2.6 2.8.3-2.1 1.9.6 2.8L4 6.2 1.5 7.6l.6-2.8L0 2.9l2.8-.3z"/><use href="#s" x="12"/><use href="#s" x="24"/><use href="#s" x="36"/></g></svg></div>
</div>
<div class="abs review" style="top:835px">
  <h4>Pellentesque habitant morbi tristique senectus</h4>
  <p>Dum accumsan vestibulum ut commodo a mi Morbi ornare gravida elit Integer conguet malesuada iaculis ipsum dui aliquet felis at cursus magna nisl</p>
  <div class="stars"><svg width="46" height="8" viewBox="0 0 46 8"><g fill="var(--star)"><use href="#s"/><use href="#s" x="12"/><use href="#s" x="24"/><use href="#s" x="36"/></g></svg></div>
</div>
<div class="abs review" style="top:897px">
  <h4>Etiam eu urna Sed porta Suspendisse</h4>
  <p>Dum accumsan vestibulum ut commodo a mi Morbi ornare gravida elit Integer con</p>
  <div class="stars"><svg width="46" height="8" viewBox="0 0 46 8"><g fill="var(--star)"><use href="#s"/><use href="#s" x="12"/><use href="#s" x="24"/><use href="#s" x="36"/></g></svg></div>
</div>

<footer>
  <div class="abs footer"></div>
  <div class="abs foot-col" style="left:113px"><h5>INFORMATION</h5><ul><li>About Us</li><li>Class Calender</li><li>Training</li><li>Join Us</li><li>Policies</li></ul></div>
  <div class="abs foot-col" style="left:222px"><h5>GROUP CLASSES</h5><ul><li>Donec dictum</li><li>Lectus non odio</li><li>Cras a ante</li><li>Citae enim iaculis</li><li>Aliquam Mauris</li></ul></div>
  <div class="abs foot-col" style="left:346px"><h5>RESOURCES</h5><ul><li>Donec dictum</li><li>Lectus non odio</li><li>Cras a ante</li><li>Citae enim iaculis</li><li>Aliquam Mauris</li></ul></div>
  <div class="abs foot-col" style="left:453px"><h5>OUR LOCATION</h5></div>
  <div class="abs map" role="img" aria-label="Street map showing the training location"></div>
  <div class="abs map-card">2870 Birchwood Ave #114<span>View larger map</span></div>
  <svg class="abs" style="left:522px;top:1089px" width="10" height="14" viewBox="0 0 10 14"><path d="M5 0a5 5 0 0 1 5 5c0 4-5 9-5 9S0 9 0 5a5 5 0 0 1 5-5z" fill="#e0302a"/><circle cx="5" cy="5" r="1.8" fill="#8a1a15"/></svg>
  <div class="abs badge"><i></i></div>
  <div class="abs bottom"></div>
  <p class="abs copy">© 2015 Company Name &nbsp;All right reserved &nbsp;Term of Use</p>
  <div class="abs social"><span style="background:#3b5a9a"></span><span style="background:#3aa0dc"></span><span style="background:#d6332a"></span></div>
</footer>

</body>
</html>
```